Creation of a construction/bricklaying business website

Following the template format of "Halloway 7", the following content would need to be included:
1. Landing page with 3 tiles that go to their own pages.
- Landing page to include background photo and description of services offered.
2. 3 tiles to include:
a) "Contact Us For A Free Quote or Friendly Discussion" Form (middle tile)
b) Case Studies and Testimonials
c) Certifications and Professional Membership
- Design logo to be used from previous SketchNestle project. Example of logo attached below, please access full JPG files from our account.

Target Market(s)

Prospective clients seeking construction work (bricklaying speciality)

Industry/Entity Type

Residential Construction

Coding

Coded - Design and coding required

Number of Pages Required

4 page

Font styles to use
Sans Serif

Colors

Designer to choose colors to be used in the design.

Requirements
Must have
• Following the template format of "Halloway 7", the following content would need to be included:
• 1. Landing parent page with 3 tiles that go to the 3 child pages.
• - Landing page to include background photo and description of services offered.
• 2. 3 tiles to include:
• a) "Contact Us For A Free Quote or Friendly Discussion" Form (middle tile)
• b) Case Studies and Testimonials (first tile / left side)
• c) Certifications and Professional Memberships (third tile / right side) (This should include logos of the relevant organisations being displayed. Specifically GQT and the Pillar Seal GQT).
• - Design logo to be used from previous SketchNestle project. Example of logo attached below, please access full JPG files from our account.
Nice to have
• Sleek and modern feel.
• Approachable in terms of how people can contact the company for a quote.
• Traditional pictures to give credibility and comfort around choosing this company.
Should not have
• Cheesy pictures
• Over-complicated
• Simple to use
• Easy URL domain name

```html
<!DOCTYPE html>
<html lang="en">
<head>
<meta charset="utf-8">
<title>R.T.Harlow Construction Ltd</title>
<link href="https://fonts.googleapis.com/css2?family=Poppins:wght@400;500;600;700&display=swap" rel="stylesheet">
<style>
:root{
  --brand-blue:#133f92;
  --navy:#0b1f3f;
  --white:#ffffff;
  --card-grey:#eeeeee;
  --text-dark:#333333;
  --text-body:#444444;
  --icon-grey:#a8a8a8;
  --badge-maroon:#9b1b2e;
  --badge-red:#d0112b;
  --badge-navy:#1b2a4a;
}
*{margin:0;padding:0;box-sizing:border-box}
html,body{width:1000px;height:1200px;overflow:hidden}
body{font-family:"Poppins",sans-serif;background:var(--white);position:relative;color:var(--text-dark)}

.hero{position:absolute;left:0;top:0;width:1000px;height:497px;overflow:hidden}
.hero-photo{position:absolute;inset:0;
  background:
    radial-gradient(ellipse 220px 160px at 640px 360px, rgba(200,120,60,.55), transparent 70%),
    linear-gradient(180deg,#1a2a44 0%,#2b3c52 45%,#3a3f3a 80%,#2a2c25 100%)}
.hero-shade{position:absolute;inset:0;background:linear-gradient(90deg,rgba(10,20,40,.55) 0%,rgba(10,20,40,.2) 60%,rgba(10,20,40,.1) 100%)}

.brand{position:absolute;left:0;top:60px;width:1000px;text-align:center;color:var(--white)}
.brand-name{font-weight:700;font-size:44px;line-height:48px;letter-spacing:.5px}
.brand-sub{font-weight:600;font-size:16px;letter-spacing:2px;margin-top:2px}

.menu-btn{position:absolute;left:868px;top:49px;width:23px;height:23px;border:1.5px solid var(--white);border-radius:50%}
.menu-btn span{position:absolute;left:6px;width:9px;height:1.5px;background:var(--white)}

.slider-dots{position:absolute;left:952px;top:213px}
.dot{position:absolute;width:11px;height:11px;border-radius:50%;background:var(--white);left:7px}
.dot.active{left:0;width:24px;height:24px;border:2px solid var(--white);background:transparent}
.dot.active::after{content:"";position:absolute;left:4px;top:4px;width:12px;height:12px;border-radius:50%;background:var(--white)}

.intro{position:absolute;left:71px;top:185px;width:430px;color:var(--white);font-size:15px;line-height:25px;font-weight:500}
.services{position:absolute;left:71px;top:279px;width:420px;display:grid;grid-template-columns:243px 170px;row-gap:14px;list-style:none}
.service{display:flex;align-items:center;gap:11px;color:var(--white);font-size:14.5px;font-weight:500;height:29px}
.service-icon{width:29px;height:29px;border-radius:50%;background:var(--white);display:flex;align-items:center;justify-content:center;flex:none}

.promise{position:absolute;left:0;top:497px;width:1000px;height:184px;background:var(--brand-blue)}
.promise-box{position:absolute;left:72px;top:19px;width:856px;height:148px;border:1.5px solid var(--white);text-align:center;color:var(--white);padding:20px 24px 0}
.promise-box p{font-size:15px;line-height:24.5px}
.promise-box a{display:inline-block;margin-top:9px;color:var(--white);font-size:15px;text-decoration:underline;text-underline-offset:3px}

.tiles{position:absolute;left:70px;top:729px;width:860px;height:365px}
.tile{position:absolute;top:0;width:283px;height:365px;background:var(--card-grey);box-shadow:0 0 8px rgba(0,0,0,.15);text-align:center}
.tile-cases{left:0}
.tile-contact{left:288px;background:var(--brand-blue);box-shadow:none;color:var(--white)}
.tile-certs{left:577px}
.tile-icon{position:absolute;left:0;width:100%;top:22px;height:70px;display:flex;justify-content:center}
.tile h2{position:absolute;left:0;top:111px;width:100%;font-size:19px;line-height:29px;font-weight:600}
.tile-contact h2{color:var(--white)}
.tile p{position:absolute;left:30px;top:175px;width:223px;font-size:13.5px;line-height:21.5px;color:var(--text-body)}
.tile-contact p{color:var(--white)}
.btn{position:absolute;left:68px;top:300px;width:146px;height:43px;border-radius:22px;background:var(--brand-blue);color:var(--white);font-size:13.5px;font-weight:700;line-height:43px;text-decoration:none;letter-spacing:.3px}
.tile-contact .btn{background:var(--white);color:var(--brand-blue)}
.badges{position:absolute;left:27px;top:193px;width:230px;height:83px}
.badge-panel{position:absolute;left:0;top:0;width:55px;height:83px;background:var(--badge-maroon)}
.badge-seal{position:absolute;left:80px;top:5px;width:143px;height:50px;background:var(--badge-navy);border-radius:3px}
.badge-bar{position:absolute;left:80px;top:66px;width:143px;height:8px;background:var(--badge-red)}

.footer{position:absolute;left:0;top:1137px;width:1000px;height:63px;background:var(--brand-blue);color:var(--white)}
.footer small{position:absolute;left:72px;top:22px;font-size:12.5px;font-weight:500}
</style>
</head>
<body>

<header class="hero">
  <div class="hero-photo" role="img" aria-label="Modern two-storey house with lit entrance and palm trees at dusk"></div>
  <div class="hero-shade"></div>

  <div class="brand">
    <div class="brand-name">R.T.Harlow</div>
    <div class="brand-sub">CONSTRUCTION LTD</div>
  </div>

  <div class="menu-btn" aria-label="Menu">
    <span style="top:6px"></span><span style="top:10px"></span><span style="top:14px"></span>
  </div>

  <div class="slider-dots">
    <div class="dot active" style="top:0"></div>
    <div class="dot" style="top:36px"></div>
    <div class="dot" style="top:59px"></div>
  </div>

  <p class="intro">R.T.Harlow Construction Ltd Is A Construction Company That Has Expertise And Experience In The Following Areas:</p>

  <ul class="services">
    <li class="service"><span class="service-icon"><svg width="17" height="17" viewBox="0 0 17 17" fill="none" stroke="#133f92" stroke-width="1.4"><rect x="2" y="6" width="10" height="8"/><path d="M2 6l5-4 5 4M12 9h3v5h-3"/></svg></span>Extensions</li>
    <li class="service"><span class="service-icon"><svg width="17" height="17" viewBox="0 0 17 17" fill="none" stroke="#133f92" stroke-width="1.4"><rect x="2" y="6" width="13" height="5" rx="2.5" transform="rotate(-40 8.5 8.5)"/><path d="M7 7l3 3"/></svg></span>Plastering</li>
    <li class="service"><span class="service-icon"><svg width="17" height="17" viewBox="0 0 17 17" fill="none" stroke="#133f92" stroke-width="1.4"><path d="M8.5 2v13M4 15h9M5 5h7M6 5v10M11 5v10"/></svg></span>New build / New houses</li>
    <li class="service"><span class="service-icon"><svg width="17" height="17" viewBox="0 0 17 17" fill="none" stroke="#133f92" stroke-width="1.4"><path d="M3 15h11M3 12h11M3 9h11M6 9v3M11 9v3M8.5 12v3M8.5 3v6"/></svg></span>Brickwork</li>
    <li class="service"><span class="service-icon"><svg width="17" height="17" viewBox="0 0 17 17" fill="none" stroke="#133f92" stroke-width="1.4"><rect x="2" y="3" width="13" height="11" rx="1"/><path d="M2 7h13M2 11h13M6 3v4M11 3v4M8.5 7v4M6 11v3M11 11v3"/></svg></span>Garden walls</li>
    <li class="service"><span class="service-icon"><svg width="17" height="17" viewBox="0 0 17 17" fill="none" stroke="#133f92" stroke-width="1.5"><path d="M2 6l6.5-3 6.5 3-6.5 3zM2 10l6.5 3 6.5-3M2 8l6.5 3 6.5-3"/></svg></span>Groundworks</li>
  </ul>
</header>

<section class="promise">
  <div class="promise-box">
    <p>We pride ourselves on attention to detail, pride in our completed project and client satisfaction. We believe in full transparency and this is reflected in the jobs we quote for you. We break down each step with both labour and materials cost so you can see exactly what you are paying for.</p>
    <a href="#contact">Feel free to get in touch and we can talk through what you are looking to achieve.</a>
  </div>
</section>

<section class="tiles">
  <article class="tile tile-cases">
    <div class="tile-icon">
      <svg width="72" height="62" viewBox="0 0 72 62" fill="var(--icon-grey)">
        <path d="M4 62V36C4 14 12 4 30 2v12c-8 2-12 8-12 16h12v32z"/>
        <path d="M40 62V36C40 14 48 4 66 2v12c-8 2-12 8-12 16h12v32z"/>
      </svg>
    </div>
    <h2>Case Studies &amp;<br>Testimonials</h2>
    <p>Sed ut perspiciatis unde omnis iste natus error sit voluptatem accusantium doloremque laudantium, totam rem aperiam, eaque ipsa quae ab</p>
    <a class="btn" href="#cases">Click Here</a>
  </article>

  <article class="tile tile-contact" id="contact">
    <div class="tile-icon" style="top:31px">
      <svg width="72" height="58" viewBox="0 0 72 58" fill="#ffffff">
        <ellipse cx="30" cy="22" rx="30" ry="21"/>
        <path d="M12 36l-6 12 16-8z"/>
        <path d="M60 18c8 4 12 11 10 19-2 6-6 10-12 12l6 9-14-7c-8 1-16-1-21-6 16 0 30-10 31-27z" stroke="#133f92" stroke-width="3"/>
      </svg>
    </div>
    <h2>Contact Us For A Free Quote<br>or Friendly Discussion</h2>
    <p>Sed ut perspiciatis unde omnis iste natus error sit voluptatem accusantium doloremque laudantium, totam rem aperiam, eaque ipsa quae ab</p>
    <a class="btn" href="#form">Contact Us</a>
  </article>

  <article class="tile tile-certs">
    <div class="tile-icon" style="top:24px">
      <svg width="58" height="72" viewBox="0 0 58 72" fill="var(--icon-grey)">
        <path d="M14 44l-8 20 10-3 5 9 8-20zM44 44l8 20-10-3-5 9-8-20z"/>
        <circle cx="29" cy="28" r="27"/>
        <circle cx="29" cy="28" r="18" fill="var(--card-grey)"/>
        <circle cx="29" cy="28" r="14"/>
        <path d="M22 28l5 5 9-10" stroke="var(--card-grey)" stroke-width="3.5" fill="none"/>
      </svg>
    </div>
    <h2>Certifications and<br>Professional Memberships</h2>
    <div class="badges">
      <div class="badge-panel" role="img" aria-label="Membership badge"></div>
      <div class="badge-seal" role="img" aria-label="Endorsed standards badge"></div>
      <div class="badge-bar"></div>
    </div>
    <a class="btn" href="#certs">Click Here</a>
  </article>
</section>

<footer class="footer">
  <small>© 2018&nbsp; Copyrights | All Rights Reserved</small>
</footer>

</body>
</html>
```